Healthcare Texting App - Web Ads

We need a variety of digital ads in the sizes of those uploaded. Vexa is a HIPAA compliant and secure mobile messaging app. Our target audience is made up of Healthcare C-suite and decision makers, mainly in the home health/hospice and behavioral healthcare industries . Vexa is a communication solution for healthcare. It is a HIPAA compliant and secure mobile app that lets healthcare providers, caregivers, doctors, nurses etc, group message, share files, make calls, and video chat etc. We currently focus on the importance of security when handling patient data. Regular SMS texting may be fast but it isn't safe or HIPAA compliant. Vexa provides both speed and security. Our goal is to get free trial requests or purchase of our App for their organization. Below are some of the current ads we have used. Feel free to take these ideas or terminology, or provide something completely new based on info from our website. You can visit getvexa-example.com to learn more about our brand and color scheme. The images from other brands are also some examples that we liked.

Target Market(s)

B2B Healthcare C suite/Decision makers, CEO, CTO - Healthcare administrators. Home Healthcare agencies, Hospice, Healthcare providers

Industry/Entity Type

Healthcare

Font styles to use
Sans Serif
Other font styles liked:
• Proxima Nova

Requirements
Nice to have
• Preferred font is Proxima Nova
• CTA button calling to start a trial, Try Vexa, request trial, start trial, get started, get secure, get compliant, etc.

```html
<!DOCTYPE html>
<html lang="en">
<head>
<meta charset="utf-8">
<title>Vexa – Web Ads</title>
<link rel="stylesheet" href="https://fonts.googleapis.com/css2?family=Figtree:wght@400;600;800&display=swap">
<style>
  :root {
    --blue-top: #49a8ea;
    --blue-bottom: #2e8ad6;
    --red: #e63a3f;
    --white: #ffffff;
    --page: #ffffff;
    --photo-a: #cfe3f1;
    --photo-b: #8fb8d8;
    --device-a: #e9eef3;
    --device-b: #b9c8d6;
  }
  * { margin: 0; padding: 0; box-sizing: border-box; }
  html, body {
    width: 1200px; height: 462px; overflow: hidden;
    background: var(--page);
    font-family: "Figtree", "Helvetica Neue", Arial, sans-serif;
  }
  .ad-set {
    width: 1200px; height: 462px;
    display: flex; flex-direction: column; justify-content: space-between;
  }
  .banner {
    position: relative; height: 146px; overflow: hidden;
    background: linear-gradient(180deg, var(--blue-top), var(--blue-bottom));
    color: var(--white);
  }
  .banner__visual {
    position: absolute; top: 0; bottom: 0; left: 0;
  }
  .banner__visual--photo {
    width: 250px;
    background: radial-gradient(circle at 40% 40%, var(--photo-a), var(--photo-b) 80%);
    clip-path: polygon(0 0, 100% 0, 82% 100%, 0 100%);
  }
  .banner__accent {
    position: absolute; left: 0; bottom: 0; width: 240px; height: 146px;
  }
  .banner__visual--devices {
    left: 20px; top: 14px; bottom: 0; width: 250px;
    background: linear-gradient(160deg, var(--device-a), var(--device-b));
    border-radius: 10px 10px 0 0;
  }
  .banner__copy {
    position: absolute; left: 260px; right: 170px; top: 0; bottom: 0;
    display: flex; flex-direction: column; justify-content: center; align-items: center;
    text-align: center; line-height: 1.15;
  }
  .banner--devices .banner__copy { left: 290px; }
  .headline-large { font-size: 42px; font-weight: 600; }
  .headline-large strong { font-weight: 800; }
  .headline { font-size: 32px; font-weight: 800; }
  .subline { font-size: 32px; font-weight: 400; margin-top: 4px; }
  .brand {
    position: absolute; right: 28px; top: 50%; transform: translateY(-50%);
    width: 96px; height: 96px; border-radius: 50%;
    background: var(--red);
    display: flex; align-items: center; justify-content: center;
    font-size: 28px; font-weight: 800; color: var(--white);
  }
</style>
</head>
<body>
<main class="ad-set">
  <section class="banner banner--photo">
    <div class="banner__visual banner__visual--photo" role="img" aria-label="Smiling doctor in a white coat holding a smartphone with a chat screen"></div>
    <div class="banner__copy">
      <p class="headline-large">Empower your team with</p>
      <p class="headline-large"><strong>simple</strong> and <strong>secure</strong> mobile messaging.</p>
    </div>
    <div class="brand">Vexa</div>
  </section>

  <section class="banner banner--devices">
    <svg class="banner__accent" viewBox="0 0 240 146" aria-hidden="true">
      <polygon points="0,40 200,146 0,146" fill="var(--red)"/>
    </svg>
    <div class="banner__visual banner__visual--devices" role="img" aria-label="Tablet and phones showing secure chat screens with an elderly patient photo"></div>
    <div class="banner__copy">
      <p class="headline">Patients trust you with their data.</p>
      <p class="subline">Make sure your tools keep them safe.</p>
    </div>
    <div class="brand">Vexa</div>
  </section>

  <section class="banner banner--devices">
    <svg class="banner__accent" viewBox="0 0 240 146" aria-hidden="true">
      <polygon points="0,40 200,146 0,146" fill="var(--red)"/>
    </svg>
    <div class="banner__visual banner__visual--devices" role="img" aria-label="Laptop and phones showing secure chat screens with an elderly patient photo"></div>
    <div class="banner__copy">
      <p class="headline">There’s more to a HIPAA breach than a fine.</p>
      <p class="subline">Protect your patients and your bottomline.</p>
    </div>
    <div class="brand">Vexa</div>
  </section>
</main>
</body>
</html>
```